I need a SEO-friendly Wordpress website (making sure to style H1, H2, H3, etc correctly) for a Hawaii-based law firm called Meridian Crest Legal Group. Comparable websites include https://brvlaw.example/ and https://www.lomrit.example/ for design reference. The current copy on the TarnAdvocate.example website can be used.

```html
<!DOCTYPE html>
<html lang="en">
<head>
<meta charset="utf-8">
<title>Meridian Crest Legal Group</title>
<link rel="stylesheet" href="https://fonts.googleapis.com/css2?family=Libre+Baskerville:wght@400;700&family=Oswald:wght@500;600&family=Raleway:ital,wght@0,400;0,500;0,600;1,500&display=swap">
<style>
:root{
  --orange:#b8620f;
  --orange-bright:#d27414;
  --brown:#8a3d06;
  --ink:#111;
  --text:#555;
  --white:#fff;
  --contact:#b4600f;
  --serif:'Libre Baskerville',Georgia,serif;
  --sans:'Raleway',Arial,sans-serif;
  --display:'Oswald','Arial Narrow',sans-serif;
}
*{margin:0;padding:0;box-sizing:border-box}
html,body{width:1200px;height:3266px;overflow:hidden}
body{position:relative;font-family:var(--sans);color:var(--text);background:var(--white)}
.abs{position:absolute}
.center{left:0;width:1200px;text-align:center}
a{color:inherit}

/* header & hero */
.hero{top:0;left:0;width:1200px;height:677px;background:linear-gradient(135deg,#3a3530 0%,#24211f 45%,#15171a 100%)}
.hero::after{content:"";position:absolute;inset:0;background:radial-gradient(ellipse at 75% 40%,rgba(120,110,95,.35),transparent 60%)}
.site-header{top:0;left:0;width:1200px;height:88px;border-bottom:1px solid rgba(255,255,255,.15);z-index:2}
.brand{left:82px;top:24px;font-family:var(--serif);font-weight:700;font-size:28px;color:var(--white)}
.nav a{position:absolute;top:38px;font-size:14.5px;letter-spacing:.4px;color:var(--white);text-decoration:none}
.nav a.active{color:var(--orange-bright)}
.nav-underline{left:553px;top:86px;width:59px;height:3px;background:var(--orange-bright)}
.phone-btn{left:1090px;top:31px;width:33px;height:33px;border-radius:50%;background:var(--orange)}
.hero-kicker{top:279px;font-size:19.5px;color:var(--white);z-index:2}
.hero-title{top:320px;font-family:var(--display);font-weight:600;font-size:46px;line-height:62px;color:var(--orange-bright);z-index:2}
.pill{border-radius:30px;background:var(--brown);box-shadow:-6px 0 0 var(--orange);color:var(--white);font-family:var(--serif);font-weight:700;font-size:17px;text-align:center;letter-spacing:.5px}
.hero-cta{left:450px;top:466px;width:300px;height:56px;line-height:56px;z-index:2}

/* about */
.about-title{left:108px;top:790px;font-family:var(--serif);font-weight:700;font-size:38px;line-height:47px;color:var(--ink)}
.kicker{font-size:16px;font-weight:600;color:var(--orange)}
.about-kicker{left:109px;top:897px}
.bar{height:3px;width:38px;background:var(--orange)}
.about-bar{left:110px;top:937px}
.about-copy{left:616px;top:746px;width:412px;font-size:13.3px;line-height:27px}
.about-copy p+p{margin-top:24px}
.about-cta{left:624px;top:1015px;width:180px;height:56px;line-height:56px}

/* practice areas */
.practice{top:1140px;left:0;width:1200px;height:625px;background:linear-gradient(160deg,#242a33 0%,#1c2027 50%,#2c2823 100%)}
.section-title{font-family:var(--serif);font-weight:700;font-size:39px;color:var(--ink)}
.practice .section-title{top:60px;color:var(--white)}
.practice-kicker{top:120px}
.practice-bar{left:581px;top:158px}
.area{left:0;width:1200px;height:67px;line-height:67px;text-align:center;font-family:var(--serif);font-size:20px;color:var(--orange);background:rgba(40,46,56,.75)}
.area.active{background:var(--orange);color:var(--white);opacity:.95}
.area svg{position:absolute;left:832px;top:13px}

/* attorneys */
.attorney-title{top:1824px}
.attorney-kicker{top:1882px;line-height:26px}
.attorney-bar{left:581px;top:1949px}
.person-name{top:1995px;width:300px;text-align:center;font-family:var(--serif);font-weight:700;font-size:19px;color:var(--ink)}
.read-more{top:2027px;width:300px;text-align:center;font-size:14.5px;font-style:italic;font-weight:500;color:var(--orange);text-decoration:underline}
.portrait{top:2065px;height:394px;border-radius:90px 90px 0 0}
.p1{left:350px;width:230px;background:linear-gradient(180deg,#e8e4e0 0%,#2b2f3a 30%,#1a1e29 100%)}
.p2{left:616px;width:214px;background:linear-gradient(180deg,#e6e2dc 0%,#3a3a3c 32%,#222 100%)}

/* blog */
.blog{top:2459px;left:0;width:1200px;height:313px;background:linear-gradient(135deg,#3a3939 0%,#2a2a2c 60%,#3b3735 100%)}
.blog-img{left:168px;top:74px;width:218px;height:166px;background:linear-gradient(135deg,#8e8477,#c9c2b6 50%,#6d7c90)}
.blog-title{left:420px;top:84px;font-family:var(--serif);font-weight:700;font-size:24px;color:var(--white)}
.blog-bar{left:424px;top:116px}
.blog-copy{left:426px;top:145px;width:612px;font-size:13.5px;line-height:28px;color:#eee}
.blog-more{left:428px;top:222px;font-size:14px;font-style:italic;font-weight:500;color:var(--orange-bright);text-decoration:underline}
.chevron{top:132px}

/* contact */
.contact{top:2772px;left:0;width:1200px;height:431px;background:var(--contact)}
.contact .section-title{top:62px}
.contact-kicker{top:118px;font-size:15.5px;font-weight:600;color:var(--white)}
.contact-bar{left:581px;top:153px;background:var(--white)}
.icon{width:54px;height:54px;border-radius:50%;background:var(--brown)}
.contact-label{font-family:var(--serif);font-weight:700;font-size:19px;color:var(--white)}
.contact-value{font-size:13.5px;color:#fbe9d6;line-height:27px}
.divider{left:598px;top:199px;width:1px;height:184px;background:rgba(255,255,255,.35)}

/* footer */
.footer{top:3203px;left:0;width:1200px;height:63px;background:#050505;color:#ddd;font-size:13px;line-height:63px;text-align:center}
</style>
</head>
<body>

<header class="abs site-header">
  <div class="abs brand">Meridian Crest Legal Group</div>
  <nav class="nav">
    <a class="active" style="left:560px">HOME</a>
    <a style="left:640px">PRACTIE AREAS</a>
    <a style="left:787px">ATTORNEY</a>
    <a style="left:901px">BLOG</a>
    <a style="left:972px">CONTACT US</a>
  </nav>
  <div class="abs nav-underline"></div>
  <div class="abs phone-btn">
    <svg width="33" height="33" viewBox="0 0 33 33"><path d="M11 9c1-.6 2-.4 2.5.4l1.5 2.6c.4.8.2 1.6-.5 2.1l-1 .7c.8 1.9 2.3 3.4 4.2 4.2l.7-1c.5-.7 1.300-.9 2.1-.5l2.6 1.5c.8.5 1 1.5.4 2.5-1 1.6-3 2.2-4.8 1.3-3.6-1.8-6.4-4.6-8.2-8.2C9.6 12 9.4 10 11 9z" fill="#fff"/></svg>
  </div>
</header>

<section class="abs hero" role="img" aria-label="Photo of attorneys meeting around a conference table before large office windows"></section>
<p class="abs center hero-kicker">Over 70 years of combined practice, specializing in:</p>
<h1 class="abs center hero-title">Personal Injury Family &amp; Divorce<br>Child Custody</h1>
<a class="abs pill hero-cta">GET FREE CONSULTATION</a>

<section>
  <h2 class="abs about-title">About The Kona<br>Lawyers Of MCLG</h2>
  <p class="abs kicker about-kicker">Lawyers Serving the Big Island and Neighboring Islands</p>
  <div class="abs bar about-bar"></div>
  <div class="abs about-copy">
    <p>The experienced attorneys in the Meridian Crest Legal Group's Kailua Kona, Hawaii office provide clients with a wide range of litigation expertise, including legal claims involving divorce &amp; family, personal injury, toxic exposures, intellectual property, and real estate.</p>
    <p>Our Kona office also offers commercial and hospitality litigation expertise on behalf of a wide variety of clients, including restaurants, hotels, property owners, and many others.</p>
  </div>
  <a class="abs pill about-cta">LEARN MORE</a>
</section>

<section class="abs practice" role="img" aria-label="Dark photo of a Lady Justice statue beside law books">
  <h2 class="abs center section-title">Our Practice Areas</h2>
  <p class="abs center kicker practice-kicker">Dedicated to making sure you receive the care and attention you need.</p>
  <div class="abs bar practice-bar"></div>
  <div class="abs area active" style="top:217px">Family &amp; Divorce<svg width="42" height="42"><circle cx="21" cy="21" r="19" fill="none" stroke="#fff" stroke-opacity=".6" stroke-width="1.5"/><path d="M18 14l7 7-7 7" fill="none" stroke="#fff" stroke-width="1.5"/></svg></div>
  <div class="abs area" style="top:289px">Personal Injury<svg width="42" height="42"><circle cx="21" cy="21" r="19" fill="none" stroke="#b8620f" stroke-width="1.5"/><path d="M18 14l7 7-7 7" fill="none" stroke="#fff" stroke-width="1.5"/></svg></div>
  <div class="abs area" style="top:363px">Corporate &amp; Intellectual Property<svg width="42" height="42"><circle cx="21" cy="21" r="19" fill="none" stroke="#b8620f" stroke-width="1.5"/><path d="M18 14l7 7-7 7" fill="none" stroke="#fff" stroke-width="1.5"/></svg></div>
  <div class="abs area" style="top:435px">Real Estate<svg width="42" height="42"><circle cx="21" cy="21" r="19" fill="none" stroke="#b8620f" stroke-width="1.5"/><path d="M18 14l7 7-7 7" fill="none" stroke="#fff" stroke-width="1.5"/></svg></div>
</section>

<section>
  <h2 class="abs center section-title attorney-title">Our Attorney</h2>
  <p class="abs center kicker attorney-kicker">Our lawyers are board-certified specialists in all fields of our practice. With over 70<br>combined years experience, you're in good hands with us.</p>
  <div class="abs bar attorney-bar"></div>
  <h3 class="abs person-name" style="left:312px">Daniel Okafor, ESQ.</h3>
  <a class="abs read-more" style="left:311px">Read More</a>
  <h3 class="abs person-name" style="left:592px">Martin Hale, ESQ.</h3>
  <a class="abs read-more" style="left:593px">Read More</a>
  <div class="abs portrait p1" role="img" aria-label="Portrait of attorney Daniel Okafor in a dark suit, arms crossed"></div>
  <div class="abs portrait p2" role="img" aria-label="Portrait of attorney Martin Hale in a suit and striped tie"></div>
</section>

<section class="abs blog" role="img" aria-label="Muted photo of a hand signing a document">
  <svg class="abs chevron" style="left:78px" width="22" height="44"><path d="M20 2L2 22l18 20" fill="none" stroke="#aaa" stroke-width="1.5"/></svg>
  <svg class="abs chevron" style="left:1100px" width="22" height="44"><path d="M2 2l18 20L2 42" fill="none" stroke="#aaa" stroke-width="1.5"/></svg>
  <div class="abs blog-img" role="img" aria-label="Photo of a couple sitting apart on a sofa"></div>
  <h3 class="abs blog-title">Top 10 Things to Do Before Filing for Divorce</h3>
  <div class="abs bar blog-bar"></div>
  <p class="abs blog-copy">No one gets married with the intention of things not working out, but it's an unfortunate fact that many marriages don't work out in the end.</p>
  <a class="abs blog-more">Read More... »</a>
</section>

<section class="abs contact">
  <h2 class="abs center section-title">Contact Us</h2>
  <p class="abs center contact-kicker">If You Have An Any Question For Contact Us Today !</p>
  <div class="abs bar contact-bar"></div>

  <div class="abs icon" style="left:283px;top:206px"><svg width="54" height="54"><path d="M20 17c1.2-.7 2.4-.5 3 .5l1.8 3c.5 1 .2 2-.6 2.5l-1.2.8c1 2.3 2.8 4.1 5.1 5.1l.8-1.2c.6-.8 1.6-1.1 2.5-.6l3 1.8c1 .6 1.2 1.8.5 3-1.2 1.9-3.6 2.6-5.8 1.5-4.3-2.2-7.7-5.6-9.900-9.900-1.100-2.200-.4-4.600 1.500-5.800z" fill="#fff"/></svg></div>
  <div class="abs contact-label" style="left:356px;top:210px">Call Us :</div>
  <div class="abs contact-value" style="left:356px;top:236px">+1.808.555.0142</div>

  <div class="abs icon" style="left:283px;top:290px"><svg width="54" height="54"><rect x="17" y="20" width="20" height="15" rx="1.5" fill="#fff"/><path d="M17 21l10 8 10-8" fill="none" stroke="#8a3d06" stroke-width="1.8"/></svg></div>
  <div class="abs contact-label" style="left:356px;top:295px">Email Us :</div>
  <div class="abs contact-value" style="left:356px;top:322px">clients@tarnadvocate.example</div>

  <div class="abs divider"></div>

  <div class="abs icon" style="left:648px;top:206px"><svg width="54" height="54"><path d="M27 15c-4.4 0-8 3.4-8 7.8 0 5.5 8 14.2 8 14.2s8-8.7 8-14.2c0-4.4-3.6-7.8-8-7.8z" fill="#fff"/><circle cx="27" cy="23" r="3" fill="#8a3d06"/></svg></div>
  <div class="abs contact-label" style="left:731px;top:205px">Meridian Crest Legal Group</div>
  <div class="abs contact-value" style="left:729px;top:240px">48-2210 Palani Way, Suite 212<br>Kailua Kona, Hawaii 96740.</div>
</section>

<footer class="abs footer">©2019 Meridian Crest Legal Group. - All Rights Reserved. Privacy Policy &nbsp;| Tearms &amp; Condition</footer>

</body>
</html>
```